Communication and Marketing agency needs a new presentation card

We are a group of communication and marketing agencies specialized in companies that are in the logistics and industrial sector. The head agency is TELVANO Grupo and the group consists of 4 agencies: TELVANO Media, TELVANO Digital, TELVANO Research and DifundeEnPantalla. We hace 4 offices in Spain (Madrid, Barcelona, Valencia and Murcia). We are looking for a clean and attractive design that transmits our experience, brand presence in the market and knowledge to those who receive the card.It has to maintain the colors of the logo that is attached.
Target Market(s)
logistics and industrial sector
Marketing department
Contact Information for Business Card
Clean and attractive design

```html
<!DOCTYPE html>
<html lang="en">
<head>
<meta charset="utf-8">
<title>TELVANO Grupo – Business Card</title>
<link href="https://fonts.googleapis.com/css2?family=Oswald:wght@500&family=Fira+Sans:wght@400;600&display=swap" rel="stylesheet">
<style>
  :root {
    --backdrop: #3a5573;
    --card-dark: #10161f;
    --card-mid: #122438;
    --brand-red: #b5262e;
    --text-light: #f2f4f7;
    --map-tone: #1c2a3a;
  }
  * { margin: 0; padding: 0; box-sizing: border-box; }
  html, body {
    width: 1200px; height: 1200px; overflow: hidden;
    background: var(--backdrop);
  }
  .canvas { position: relative; width: 1200px; height: 1200px; }
  .card {
    position: absolute; left: 193px; width: 814px; height: 466px;
    background: radial-gradient(ellipse at 55% 60%, var(--card-mid) 0%, var(--card-dark) 75%);
    overflow: hidden;
  }
  .card--front { top: 76px; }
  .card--back { top: 658px; }
  .world-map {
    position: absolute; inset: 30px 0 0 0;
    background: radial-gradient(ellipse at 50% 45%, var(--map-tone) 0%, rgba(28,42,58,0) 70%);
    opacity: .8;
  }
  .wordmark {
    position: absolute; display: flex; flex-direction: column; align-items: flex-end;
    font-family: "Oswald", sans-serif; font-weight: 500; color: var(--brand-red);
    line-height: 1;
  }
  .wordmark__name { font-size: 92px; letter-spacing: 6px; }
  .wordmark__group { font-size: 60px; margin-top: 4px; }
  .card--front .wordmark { left: 186px; top: 170px; width: 444px; }
  .card--back .wordmark { left: 286px; top: 52px; width: 442px; }
  .person { position: absolute; left: 68px; top: 250px; }
  .person__name {
    font-family: "Oswald", sans-serif; font-weight: 500; font-size: 37px;
    color: var(--brand-red); letter-spacing: .5px; line-height: 1.1;
  }
  .person__role {
    font-family: "Fira Sans", sans-serif; font-size: 17px; color: var(--text-light);
    margin-top: 8px; letter-spacing: .5px;
  }
  .divider { display: block; margin: 14px 0 10px 4px; }
  .details {
    font-family: "Fira Sans", sans-serif; font-size: 17.5px; line-height: 23.5px;
    color: var(--text-light);
  }
  .details b { font-weight: 600; }
  .details .accent { color: var(--brand-red); }
  .address { position: absolute; left: 540px; top: 330px; }
  .address .divider { margin: 0 0 10px 0; }
</style>
</head>
<body>
<main class="canvas">
  <section class="card card--front">
    <div class="world-map" role="img" aria-label="Faint world map in dark navy tones"></div>
    <div class="wordmark">
      <span class="wordmark__name">TELVANO</span>
      <span class="wordmark__group">Grupo</span>
    </div>
  </section>

  <section class="card card--back">
    <div class="wordmark">
      <span class="wordmark__name">TELVANO</span>
      <span class="wordmark__group">Grupo</span>
    </div>

    <div class="person">
      <h1 class="person__name">MARCO ELLISON</h1>
      <p class="person__role">MANAGER</p>
      <svg class="divider" width="38" height="8" viewBox="0 0 38 8" aria-hidden="true">
        <circle cx="4" cy="4" r="3.5" fill="var(--brand-red)"/>
        <line x1="6" y1="4" x2="38" y2="4" stroke="var(--brand-red)" stroke-width="1.5"/>
      </svg>
      <p class="details">
        <b>P.</b>&nbsp; +(415)&nbsp; -555- 0192<br>
        <b>F.</b> +(415)&nbsp; -555- 0192<br>
        contact@telvanomail.com
      </p>
    </div>

    <div class="address">
      <svg class="divider" width="38" height="8" viewBox="0 0 38 8" aria-hidden="true">
        <circle cx="4" cy="4" r="3.5" fill="var(--brand-red)"/>
        <line x1="6" y1="4" x2="38" y2="4" stroke="var(--brand-red)" stroke-width="1.5"/>
      </svg>
      <p class="details">
        840 North Harlow Avenue,<br>
        Linden, NE 68214<br>
        www.<span class="accent">telvanogroup</span>.com
      </p>
    </div>
  </section>
</main>
</body>
</html>
```